Exclusive beauty salon needs a price list or services booklet

I need a new very attractive flyer for my beauty salon, containing information on the different services and their prices.
In attachment you can find a pdf of the "old" one, but I'd love to have a beautifully designed new one!
I'd love to have a booklet in format 148 x 148 mm, or in US format, containing 12 or 16 pages, but if you can offer other nice looking designs they are welcome!
The services that need to come in the booklet with their prices can all be found on my website: www.atelierverano.be, starting with
Gelaatsverzorging
Wimperverlenging
Suikerontharing
Wimperlifting
Permanente Make Up
Airbrush Tanning

Target Market(s)

woman from 20 to 89 years old

Industry/Entity Type

Beauty Salon

Font styles to use
Sans Serif

Colors

Designer to choose colors to be used in the design.

Requirements
Must have
• a classy nice look, it must contain details about the services from my beauty salon and their prices, and nice pictures.
• The Names, prices and explanations of the services can easily be found on my website: www.atelierverano.be
Nice to have
• In attachment you can find the "old" price list in pdf, what I need now is a "new booklet" with the new logo and updated services price list.
• I need a very nice and attractive looking booklet, classy chique, Paris chique, looking very expensive.
Should not have
• Not too much colors, not too curly, but still feminine

```html
<!DOCTYPE html>
<html lang="nl">
<head>
<meta charset="utf-8">
<title>Atelier Verano – Gelaatsverzorging</title>
<link rel="stylesheet" href="https://fonts.googleapis.com/css2?family=Open+Sans:wdth,wght@75..100,300..800&display=swap">
<style>
  :root{
    --backdrop:#fbe5e7;
    --paper:#efe7e8;
    --paper-light:#f6f1f1;
    --rose:#d9a3a8;
    --rose-soft:#ecc6c9;
    --charcoal:#48484b;
    --ink:#4d4d50;
    --ink-soft:#6a6a6d;
  }
  *{box-sizing:border-box;margin:0;padding:0}
  html,body{width:1200px;height:797px;overflow:hidden}
  body{background:var(--backdrop);font-family:"Open Sans",Arial,sans-serif;color:var(--ink)}
  .spread{position:absolute;left:60px;top:128px;width:1080px;height:540px;display:flex;box-shadow:0 14px 40px rgba(120,70,80,.18)}
  .page{position:relative;width:540px;height:540px;overflow:hidden;background:linear-gradient(160deg,var(--paper-light),var(--paper))}
  .page--left{box-shadow:inset -18px 0 24px -18px rgba(0,0,0,.18)}
  .page--right{box-shadow:inset 18px 0 24px -18px rgba(0,0,0,.14)}
  .page-art{position:absolute;left:0;top:0}

  .brand{position:absolute;left:38px;top:222px;display:flex;align-items:center;gap:9px}
  .brand-mark{width:12px;height:12px;background:var(--charcoal)}
  .brand-name{font-size:13px;font-weight:400;letter-spacing:.28em;text-transform:uppercase;color:var(--charcoal)}

  .title-box{position:absolute;left:0;top:266px;width:290px;padding:11px 18px 11px 34px;background:var(--charcoal)}
  .title-box h1{font-size:19px;line-height:1.12;font-weight:700;font-stretch:80%;color:#fff}

  .intro{position:absolute;left:34px;top:364px;width:380px;font-size:10px;line-height:1.4;color:var(--ink-soft);text-align:justify}
  .intro p{margin-bottom:6px}
  .intro ul{list-style:none;padding-left:60px}
  .intro li::before{content:"> ";font-weight:700}

  .services{position:absolute;left:30px;right:30px;top:268px;text-align:center;font-size:10.5px;line-height:1.45;color:var(--ink)}
  .service{margin-bottom:4px}
  .service h2{display:block;margin:0 -30px 2px;padding:2px 0;font-size:17px;font-weight:700;font-stretch:78%;color:var(--charcoal);
    background:linear-gradient(90deg,transparent 0%,var(--rose-soft) 25%,var(--rose) 50%,var(--rose-soft) 75%,transparent 100%)}
  .service .price{font-size:13px;font-weight:800;color:#222;white-space:nowrap}
</style>
</head>
<body>
  <main class="spread">
    <section class="page page--left">
      <svg class="page-art" width="540" height="540" viewBox="0 0 540 540">
        <defs>
          <radialGradient id="leftPhotoTone" cx="60%" cy="45%" r="60%">
            <stop offset="0" stop-color="#f3dcd6"/>
            <stop offset=".55" stop-color="#e4b7b5"/>
            <stop offset="1" stop-color="#d39da2"/>
          </radialGradient>
        </defs>
        <circle cx="380" cy="60" r="227" fill="var(--charcoal)"/>
        <circle cx="386" cy="52" r="215" fill="url(#leftPhotoTone)" role="img" aria-label="Close-up portret van een vrouw met een verzorgde, stralende huid"/>
      </svg>

      <div class="brand">
        <span class="brand-mark"></span>
        <span class="brand-name">Atelier Verano</span>
      </div>

      <div class="title-box">
        <h1>Gelaatsverzorging<br>met de kwalitatieve<br>producten van Lumiane</h1>
      </div>

      <div class="intro">
        <p>“Een antwoord bieden voor iedere huidconditie, omdat deze uniek is”</p>
        <p>Het merk Lumiane heeft een uitgebreid aanbod aan gelaatsverzorgingen, geschikt voor alle “huidproblemen”. Na een persoonlijke huidanalyse wordt een verzorging uitgevoerd die bij u past. Naast de cabineverzorgingen, kan je ook advies krijgen voor de dagelijkse verzorging thuis.</p>
        <p>Gelaatsverzorgingen van Lumiane bieden:</p>
        <ul>
          <li>een combinatie van plezier en welzijn</li>
          <li>een unieke ervaring voor de zintuigen</li>
          <li>resultaatgerichte behandelingen</li>
        </ul>
      </div>
    </section>

    <section class="page page--right">
      <svg class="page-art" width="540" height="540" viewBox="0 0 540 540">
        <defs>
          <linearGradient id="rightPhotoTone" x1="0" y1="0" x2="1" y2="1">
            <stop offset="0" stop-color="#d9a1a6"/>
            <stop offset=".6" stop-color="#e6bdbb"/>
            <stop offset="1" stop-color="#d7a0a5"/>
          </linearGradient>
        </defs>
        <path d="M0 0H540V118Q330 265 0 258Z" fill="var(--charcoal)"/>
        <path d="M0 0H540V104Q330 250 0 246Z" fill="url(#rightPhotoTone)" role="img" aria-label="Glimlachende vrouw met gesloten ogen en hand tegen de wang"/>
      </svg>

      <div class="services">
        <article class="service">
          <h2>Cosmetische Verzorging</h2>
          <p>Verzorging i.s.v. Dermatoloog</p>
          <p>De verzorging bestaat uit: oppervlakkige reiniging, verwijderen zwarte puntjes en onzuiverheden, zuiverend masker. <span class="price">€30</span></p>
        </article>
        <article class="service">
          <h2>Verwijderen van gerstekorrels</h2>
          <p>De prijs is afhankelijk van de hoeveelheid, vanaf <span class="price">€15</span>, afhankelijk van de hoeveelheid</p>
        </article>
        <article class="service">
          <h2>Éclat Express</h2>
          <p>Voor een gehydrateerde en comfortabele huid. Voor alle huidtypes, bij een vermoeide huid met weinig uitstraling. De verzorging bestaat uit: epilatie wenkbrauwen, oppervlakkige reiniging, diepe reiniging, crememasker aangepast aan huidconditie, serum, dagcrème, handmassage <span class="price">€59 - 50 min.</span></p>
        </article>
      </div>
    </section>
  </main>
</body>
</html>
```